Simple Business Card Design for Tavlo

Job:

Make a very simple, minimalist business card design with my details including adjusted logo. One side to be white (with logo & text). Other side to be yellow - try plain or with logo (or part of logo eg Z). Need business card to have continuity with website.

Logo:
Our logo is made from a free download font website:
http://www.typewell.net/search.php?q=rubber
but the spacing/kerning needs correcting/adjusting as the font spaces unevenly between letters (see attached files). Need logo to be very crisp/sharp when printed.

Printing:
We will be using Plika.com so the design needs to conform to their requirements, see here:

http://uk.plika.com/products/luxe/business-cards.html (scroll down for dimensions and guidelines)

Design:

must say "plant-based food consulting" underneath logo or somewhere
no address needed in contact section
sharp corners (not rounded)
one side white, one side yellow

name: Rosalind Whitcombe
1xmobile number: +44 7700900463
1xtwiiter: @brimcounsel
website address www.orchardtable.com
email address brim@orchardtable.com

Should be easy quick job, prompt + detailed feedback given, am online in UK 9am-10pm for next 3 days. Website is www.orchardtable.com

Industry/Entity Type

Business

Requirements
Must have
• The logo must be corrected. The kerning is not right.

Please use a warm-grey for text

Please submit in matt format, we will be printing matt finish.

Should not have
• Avoid using banners or curvy highlights

Please avoid using black

Please avoid submitting in gloss finish

```html
<!DOCTYPE html>
<html lang="en">
<head>
<meta charset="utf-8">
<title>Brim business card</title>
<link href="https://fonts.googleapis.com/css2?family=Cinzel:wght@400;700&display=swap" rel="stylesheet">
<style>
  :root {
    --backdrop: #e4e4e4;
    --card-white: #fbfaf8;
    --card-yellow: #ece04e;
    --accent: #ece04e;
    --band-light: #e6e3de;
    --warm-grey: #6f6861;
    --warm-grey-dark: #57504a;
    --rule: #c9c3bc;
  }
  * { margin: 0; padding: 0; box-sizing: border-box; }
  html, body {
    width: 1200px; height: 720px; overflow: hidden;
    background: var(--backdrop);
    font-family: "Cinzel", serif;
  }
  .canvas { position: relative; width: 1200px; height: 720px; }
  .card {
    position: absolute; top: 242px;
    width: 420px; height: 240px;
    overflow: hidden;
  }
  .card--front { left: 147px; background: var(--card-white); }
  .card--back { left: 633px; background: var(--card-yellow); }

  .wordmark {
    position: absolute;
    color: var(--warm-grey-dark);
    font-family: "Cinzel", serif;
    font-weight: 700;
    line-height: 1;
    letter-spacing: 0.04em;
  }
  .card--front .wordmark { left: 22px; top: 30px; font-size: 52px; }
  .card--back .wordmark {
    left: 0; right: 0; top: 80px; text-align: center; font-size: 70px;
  }
  .tagline {
    position: absolute;
    color: var(--warm-grey);
    font-size: 8.5px;
    letter-spacing: 0.06em;
    white-space: nowrap;
  }
  .card--front .tagline { left: 24px; top: 88px; }
  .card--back .tagline { left: 0; right: 0; top: 160px; text-align: center; font-size: 11px; }

  .holder {
    position: absolute; right: 20px; top: 106px; text-align: right;
  }
  .holder__name {
    color: var(--warm-grey-dark); font-weight: 700; font-size: 13px; line-height: 1.1;
  }
  .holder__role {
    color: var(--warm-grey); font-size: 9px; letter-spacing: 0.02em; margin-top: 1px;
  }
  .divider {
    position: absolute; left: 22px; right: 20px; top: 145px;
    height: 1px; background: var(--rule);
  }
  .contacts {
    position: absolute; left: 22px; top: 158px; list-style: none;
  }
  .contacts li {
    display: flex; align-items: center; gap: 8px;
    height: 12px; color: var(--warm-grey); font-size: 8.5px;
  }
  .contacts svg { width: 10px; height: 9px; flex: none; }
  .base-bands { position: absolute; left: 0; bottom: 0; width: 420px; height: 21px; }
</style>
</head>
<body>
<main class="canvas">
  <section class="card card--front" aria-label="Card front">
    <div class="wordmark">BRIM</div>
    <div class="tagline">PLANT-BASED FOOD CONSULTING</div>
    <div class="holder">
      <div class="holder__name">Rosalind Whitcombe</div>
      <div class="holder__role">MANAGER</div>
    </div>
    <div class="divider"></div>
    <ul class="contacts">
      <li>
        <svg viewBox="0 0 10 9" aria-hidden="true"><path fill="#6f6861" d="M1 3 Q5 0 9 3 L8 4 L6.5 3.2 L6.5 2.4 Q5 2 3.5 2.4 L3.5 3.2 L2 4 Z M2.5 4.5 H7.5 L8.5 8.5 H1.5 Z"/></svg>
        +44 7700 900463
      </li>
      <li>
        <svg viewBox="0 0 10 9" aria-hidden="true"><rect x="0.5" y="1" width="9" height="7" fill="#6f6861"/><path d="M0.8 1.5 L5 5 L9.2 1.5 M0.8 7.6 L3.8 4.2 M9.2 7.6 L6.2 4.2" stroke="#fbfaf8" stroke-width="0.9" fill="none"/></svg>
        brim@orchardtable.com
      </li>
      <li>
        <svg viewBox="0 0 10 9" aria-hidden="true"><rect x="0.8" y="0.8" width="8.4" height="5.6" fill="none" stroke="#6f6861" stroke-width="1.4"/><rect x="3" y="7.3" width="4" height="1.2" fill="#6f6861"/></svg>
        www.orchardtable.com
      </li>
      <li>
        <svg viewBox="0 0 10 9" aria-hidden="true"><circle cx="5" cy="4.5" r="3.8" fill="#6f6861"/></svg>
        @brimcounsel
      </li>
    </ul>
    <svg class="base-bands" viewBox="0 0 420 21" aria-hidden="true">
      <polygon points="0,13 300,13 296,21 0,21" fill="var(--band-light)"/>
      <polygon points="323,0 420,0 420,21 303,21" fill="var(--accent)"/>
    </svg>
  </section>

  <section class="card card--back" aria-label="Card back">
    <div class="wordmark">BRIM</div>
    <div class="tagline">PLANT-BASED FOOD CONSULTING</div>
  </section>
</main>
</body>
</html>
```